Request for Business Card Design

Hi. My name is Marlene, I am looking for a new business card design for my company, Quarrow Signal Instruments, LLC. I really like the design you did for Tarsel Venture and was hoping you could do something similar using our full logo and our mark. I am also open to any raised texture design using our mark. I have attached our full logo, which would need to be somewhere on the card, as well as the mark in both outline and full form, as well as our brand colors / guide. The card does not have to be white, as long as our logo and mark appear. I actually like darker colored business cards more, but am open to all options. If you are interested in working with me, please let me know. We would also take the business card design into letterhead design if you can do that.

```html
<!DOCTYPE html>
<html lang="en">
<head>
<meta charset="utf-8">
<title>Quarrow Signal Instruments – Business Card</title>
<link href="https://fonts.googleapis.com/css2?family=Open+Sans:wght@400;600&family=Titillium+Web:wght@700&display=swap" rel="stylesheet">
<style>
  :root {
    --backdrop: #e3e4e6;
    --card: #3c3d40;
    --accent: #1b9bcb;
    --ink: #ffffff;
    --ink-soft: #e6e7e9;
    --decor: #3f4d57;
  }
  * { margin: 0; padding: 0; box-sizing: border-box; }
  html, body { width: 1200px; height: 800px; overflow: hidden; }
  body {
    background: var(--backdrop);
    font-family: "Open Sans", Arial, sans-serif;
    position: relative;
  }
  .card {
    position: absolute;
    width: 525px;
    height: 300px;
    background: var(--card);
    overflow: hidden;
    top: 250px;
    box-shadow: 0 6px 18px rgba(0,0,0,.18);
  }
  .card--front { left: 50px; }
  .card--back { left: 625px; }

  .decor-circle {
    position: absolute;
    border-radius: 50%;
    background: var(--decor);
  }
  .card--front .decor-circle { width: 260px; height: 260px; right: -40px; bottom: -110px; }
  .card--back .decor-circle { width: 240px; height: 240px; right: -30px; bottom: -100px; }

  .brand {
    position: absolute;
    display: flex;
    align-items: center;
    gap: 14px;
  }
  .brand__dot {
    flex: none;
    border-radius: 50%;
    background: var(--accent);
  }
  .brand__name {
    font-family: "Titillium Web", Arial, sans-serif;
    font-weight: 700;
    color: var(--ink);
    text-transform: uppercase;
    line-height: 1.05;
  }
  .card--front .brand { left: 60px; top: 100px; }
  .card--front .brand__dot { width: 54px; height: 54px; }
  .card--front .brand__name { font-size: 30px; letter-spacing: 3px; }
  .card--front .brand__name small { display: block; font-size: 13px; letter-spacing: 1.6px; }

  .card--back .brand { right: 30px; top: 40px; }
  .card--back .brand__dot { width: 40px; height: 40px; }
  .card--back .brand__name { font-size: 24px; letter-spacing: 2.5px; }
  .card--back .brand__name small { display: block; font-size: 10.5px; letter-spacing: 1.3px; }

  .contact {
    position: absolute;
    left: 28px;
    top: 36px;
    width: 270px;
  }
  .contact__name {
    color: var(--accent);
    font-weight: 600;
    font-size: 14px;
    letter-spacing: .5px;
    text-transform: uppercase;
  }
  .contact__role {
    color: var(--ink-soft);
    font-size: 12px;
    margin-bottom: 14px;
  }
  .contact__list { list-style: none; }
  .contact__item {
    display: flex;
    align-items: center;
    gap: 8px;
    color: var(--ink-soft);
    font-size: 11.5px;
    line-height: 20px;
  }
  .contact__item svg { width: 11px; height: 11px; flex: none; fill: none; stroke: var(--accent); stroke-width: 1.6; }
  .contact__rule {
    border: 0;
    height: 1px;
    background: var(--accent);
    margin: 10px 0 8px;
    width: 330px;
  }
</style>
</head>
<body>

  <section class="card card--front" aria-label="Card front">
    <div class="decor-circle" aria-hidden="true"></div>
    <div class="brand">
      <span class="brand__dot" aria-hidden="true"></span>
      <p class="brand__name">Quarrow<small>Signal Instruments</small></p>
    </div>
  </section>

  <section class="card card--back" aria-label="Card back">
    <div class="decor-circle" aria-hidden="true"></div>
    <div class="brand">
      <span class="brand__dot" aria-hidden="true"></span>
      <p class="brand__name">Quarrow<small>Signal Instruments</small></p>
    </div>

    <div class="contact">
      <p class="contact__name">Dr. Corin Halvorsen</p>
      <p class="contact__role">President &amp; CEO</p>
      <ul class="contact__list">
        <li class="contact__item">
          <svg viewBox="0 0 12 12"><path d="M2 1h2.5l1 3-1.5 1a6 6 0 0 0 3 3l1-1.5 3 1V11A9 9 0 0 1 1 2z"/></svg>
          +001 555 210 4837
        </li>
        <li class="contact__item">
          <svg viewBox="0 0 12 12"><rect x="1.5" y="4" width="9" height="5"/><rect x="3.5" y="1" width="5" height="3"/><rect x="3.5" y="8" width="5" height="3"/></svg>
          +001 555 210 4852
        </li>
        <li class="contact__item">
          <svg viewBox="0 0 12 12"><rect x="1" y="2.5" width="10" height="7"/><path d="M1 2.5l5 4 5-4"/></svg>
          info@quarrowsignal.com
        </li>
        <li class="contact__item">
          <svg viewBox="0 0 12 12"><circle cx="6" cy="6" r="5"/><path d="M1 6h10M6 1c-3 3-3 7 0 10M6 1c3 3 3 7 0 10"/></svg>
          www.quarrowsignal.com
        </li>
      </ul>
      <hr class="contact__rule">
      <p class="contact__item">
        <svg viewBox="0 0 12 12"><path d="M6 11S2 7 2 4.5a4 4 0 0 1 8 0C10 7 6 11 6 11z"/><circle cx="6" cy="4.5" r="1.3"/></svg>
        1850 Ridgeway Court, Alder Falls, CO 80999
      </p>
    </div>
  </section>

</body>
</html>
```